Brochure for a website accessibility report

This brochure is related to a report that www.qelvantrix.org sell. The report shows the results of an automated audit of a websites accessibility. It shows details of issues found with screen shots, examples of code and provides remediation advice.

The brochure will be a pdf 8.5 inches by 11 inches. It can be anywhere from 6 to 10 pages.

The FlintVue™ name itself should be “Bree Serif” font. The fonts, styles, colors and sizes are up to you.

The images used and logo of the Office of Digital Reachworks and K7P logo are upload

We highlighted in blue page extracts from the report we sell. Do not use the blue highlight, it is merely there to show you where the specific examples of the report we sell are vs the other content in the report. The areas in blue which show the content from the actual report should be shown as an extract of the actual page of the report. You have flexibility to change the layout and the way the content look.

The red square callouts over the blue content are callouts that describe the specific page extracts. We used it as a red callout only so that you would be able to see it. You should change the specific location, look and feel of the callout to be appropriate

Target Market(s)

Marketing and Technical people

Industry/Entity Type

Information Technology

Font styles to use
Sans Serif

Colors

Designer to choose colors to be used in the design.

Requirements
Should not have
• wheelchairs, images of blind people

```html
<!DOCTYPE html>
<html lang="en">
<head>
<meta charset="utf-8">
<title>FlintVue™ Report Brochure – Pages 6–7</title>
<link rel="stylesheet" href="https://fonts.googleapis.com/css2?family=Bree+Serif&family=Raleway:wght@400;500;700;800&family=Source+Code+Pro:wght@400&display=swap">
<style>
  :root{
    --green:#1fa360;
    --green-light:#3cba7c;
    --orange:#ee8410;
    --orange-light:#f6b53c;
    --ink:#2c2f33;
    --muted:#5a5f66;
    --paper:#ffffff;
    --backdrop:#e4e5e7;
    --code-bg:#f4ede4;
    --rule:#cfd3d6;
  }
  *{box-sizing:border-box;margin:0;padding:0}
  html,body{width:1200px;height:840px;overflow:hidden}
  body{background:var(--backdrop);font-family:"Raleway",sans-serif;color:var(--ink);position:relative}
  .spread{position:absolute;left:40px;top:57px;width:1120px;height:725px;display:flex;box-shadow:0 10px 30px rgba(0,0,0,.12)}
  .page{position:relative;width:560px;height:725px;background:var(--paper);overflow:hidden}
  .page--left{box-shadow:inset -18px 0 22px -18px rgba(0,0,0,.18)}
  .page--right{box-shadow:inset 18px 0 22px -18px rgba(0,0,0,.14)}

  .brand{position:absolute;left:30px;top:26px;display:flex;align-items:center;gap:7px}
  .brand__mark{width:14px;height:14px;background:var(--green)}
  .brand__name{font-weight:800;font-size:8px;line-height:1.05;text-transform:uppercase;color:var(--ink);width:70px}
  .header-rule{position:absolute;left:170px;right:30px;top:44px;border-top:1px solid var(--rule)}
  .edition{position:absolute;right:30px;top:58px;font-family:"Bree Serif",serif;font-size:10px;color:var(--green)}

  /* left page */
  .section-tag{position:absolute;left:30px;top:92px;width:330px;height:40px;background:var(--green);color:#fff;font-family:"Bree Serif",serif;font-weight:400;font-size:20px;line-height:40px;padding-left:14px}
  .section-tag__chevron{position:absolute;right:12px;top:11px}
  .intro{position:absolute;left:30px;top:146px;width:470px;font-size:11px;line-height:1.45;color:var(--muted)}
  .themes{position:absolute;left:30px;top:196px;width:490px;list-style:none}
  .themes li{border:1px solid var(--green-light);height:26px;margin-bottom:4px;font-size:11px;line-height:24px;padding-left:24px;position:relative;color:var(--muted)}
  .themes li::before{content:"";position:absolute;left:9px;top:8px;width:8px;height:8px;border-radius:50%;background:var(--orange)}
  .themes b{color:var(--ink);font-weight:800}
  .detail{position:absolute;left:30px;top:385px;width:470px;font-size:10.5px;line-height:1.45;color:var(--muted)}
  .footer-band{position:absolute;left:0;right:0;top:465px;bottom:0;background:var(--green)}
  .promo{position:absolute;left:0;top:482px;width:560px;height:170px;background:linear-gradient(100deg,var(--orange) 0%,var(--orange) 45%,var(--orange-light) 100%);clip-path:polygon(0 8%,100% 0,100% 88%,0 100%)}
  .promo__text{position:absolute;left:34px;top:28px;width:490px;font-family:"Bree Serif",serif;font-size:21px;line-height:1.3;color:#fff}
  .folio{position:absolute;left:30px;bottom:22px;font-size:9px;color:rgba(255,255,255,.85)}
  .site{position:absolute;right:30px;bottom:22px;font-size:9px;font-weight:700;color:#fff}
  .foot-rule{position:absolute;left:60px;right:130px;bottom:27px;border-top:1px solid rgba(255,255,255,.35)}

  /* right page */
  .topic{position:absolute;left:30px;top:78px;font-family:"Bree Serif",serif;font-weight:400;font-size:34px;line-height:1.1;color:var(--green)}
  .topic-lede{position:absolute;left:30px;top:126px;width:230px;font-size:11.5px;font-weight:800;line-height:1.3}
  .guidance{position:absolute;left:300px;top:112px;width:230px;background:var(--green-light);color:#fff;padding:12px 14px 12px 16px;font-size:9.5px;line-height:1.45;list-style:none}
  .guidance li{position:relative;padding-left:13px;margin-bottom:6px}
  .guidance li:last-child{margin-bottom:0}
  .guidance li::before{content:"";position:absolute;left:0;top:4px;width:7px;height:7px;border-radius:50%;background:var(--orange)}
  .issue{position:absolute;left:30px;top:206px;font-family:"Bree Serif",serif;font-weight:400;font-size:24px;line-height:1.2;color:var(--ink)}
  .issue span{color:var(--green)}
  .issue-rule{position:absolute;left:30px;top:244px}
  .issue-summary{position:absolute;left:30px;top:262px;width:200px;font-size:11px;font-weight:800;line-height:1.35}
  .callout{position:absolute;left:320px;top:272px;width:210px;background:var(--orange);color:#fff;font-size:9px;font-weight:700;line-height:1.4;padding:8px 12px}
  .issue-body{position:absolute;left:250px;top:338px;width:280px;font-size:9.5px;line-height:1.45;color:var(--muted)}
  .issue-body a{color:var(--green);font-weight:700}
  .advice{position:absolute;left:0;right:0;top:460px;bottom:0;background:var(--green);color:#fff}
  .advice__title{position:absolute;left:30px;top:16px;font-family:"Bree Serif",serif;font-weight:400;font-size:20px;line-height:1.25}
  .advice__lead{position:absolute;left:30px;top:44px;width:500px;font-size:10px;line-height:1.45}
  .advice__label{position:absolute;font-weight:800;font-size:9.5px;line-height:1.2}
  .advice__label--before{left:30px;top:80px}
  .advice__label--after{left:290px;top:148px}
  .code{position:absolute;background:var(--code-bg);color:var(--ink);font-family:"Source Code Pro",monospace;font-size:9px;line-height:1.4;padding:7px 10px;border-left:3px solid var(--orange);white-space:pre}
  .code--before{left:30px;top:96px;width:250px}
  .code--after{left:290px;top:164px;width:240px}
  .advice__note{position:absolute;left:30px;top:160px;width:245px;font-size:9px;line-height:1.45;color:rgba(255,255,255,.92)}
</style>
</head>
<body>
<main class="spread">
  <section class="page page--left">
    <div class="brand"><span class="brand__mark"></span><span class="brand__name">Office of Digital Reachworks</span></div>
    <div class="header-rule"></div>
    <div class="edition">2019 Brochure</div>

    <h2 class="section-tag">Section 2
      <svg class="section-tag__chevron" width="18" height="18" viewBox="0 0 18 18" aria-hidden="true"><circle cx="9" cy="9" r="9" fill="#fff"/><path d="M5.5 7.5 9 11l3.5-3.5" fill="none" stroke="#1fa360" stroke-width="1.8"/></svg>
    </h2>
    <p class="intro">The next section of the report is designed specifically for your developers and programmers who will be in-the-trenches fixing the actual issues. The issues are prioritized and organized by six themes:</p>
    <ul class="themes">
      <li><b>Media:</b> problems related to imagery, video and plug-ins.</li>
      <li><b>Structure:</b> problems related to HTML layout markup and positioning of data.</li>
      <li><b>Text:</b> problems related to actual textual content and its comprehension.</li>
      <li><b>Scripting:</b> problems related to Scripting, e.g. in JavaScript code.</li>
      <li><b>CSS:</b> problems related to Cascading Style Sheets &amp; inline Styles.</li>
      <li><b>Form:</b> problems related to Form controls, navigability &amp; comprehension.</li>
    </ul>
    <p class="detail">Within each classification above, we provide specific details about each violation found, which URLs they were present on, code snippets, and screenshots showing you the actual violation. Remediation advice is then given to you with resource links and explanations of the guidelines your website doesn't meet.</p>

    <div class="footer-band"></div>
    <div class="promo"><p class="promo__text">The following pages provide six examples of how our FlintVue™ report shows you how to fix the violations based on the classifications listed above.</p></div>
    <div class="foot-rule"></div>
    <span class="folio">6</span>
    <span class="site">www.qelvantrix.org</span>
  </section>

  <section class="page page--right">
    <div class="brand"><span class="brand__mark"></span><span class="brand__name">Office of Digital Reachworks</span></div>
    <div class="header-rule"></div>
    <div class="edition">2019 Brochure</div>

    <h2 class="topic">Media</h2>
    <p class="topic-lede">Ensure that all Media items such as animations/video and audio have an alternative means of understanding the content.</p>
    <ul class="guidance">
      <li>Provide a text alternative for either via a transcript, audio description, sign language, or captioning (open or closed.)</li>
      <li>Additionally, any content provided through an object, Embed, or Applet (or similar 3rd party plugin) must be checked for appropriate keyboard accessible controls.</li>
    </ul>

    <h3 class="issue">Issue: <span>Image Link Text</span></h3>
    <svg class="issue-rule" width="280" height="10" viewBox="0 0 280 10" aria-hidden="true"><circle cx="5" cy="5" r="4" fill="#ee8410"/><line x1="9" y1="5" x2="280" y2="5" stroke="#ee8410" stroke-width="1.2"/></svg>
    <p class="issue-summary">Image ALT attribute text of images within links should not duplicate the text of the link body (link text.)</p>
    <p class="callout">We test for hundreds of issues. Each issue that is discovered is detailed under its specific classification the issue resided.</p>
    <p class="issue-body">Don't use the same text in an image ALT as the link containing the image. If the link text and the image alt are the same, this creates a "stutter" when screen readers read the content of the link and then the image. When the image doesn't describe any additional information beyond the link text, authors should set the image alt to "". Issue is relevant to checkpoints: <a>1.1.1 (A)</a>, <a>2.4.4 (A)</a>, <a>4.1.2 (A)</a></p>

    <div class="advice">
      <h3 class="advice__title">General Remediation Advice:</h3>
      <p class="advice__lead">When dealing with images directly contained within links with link text, don't use the same text in the image alt text as the link text.</p>
      <p class="advice__label advice__label--before">Before:</p>
      <pre class="code code--before">&lt;a href="products.html"&gt;&lt;img src="prod-
ucts.gif" alt="Products page"/&gt;Products
page&lt;/a&gt;</pre>
      <p class="advice__note">This leads to a "stutter" as screen readers will read "Products page" twice: once for the image and once for the link. Replace the alt text with "".</p>
      <p class="advice__label advice__label--after">After:</p>
      <pre class="code code--after">&lt;a href="products.html"&gt;&lt;img src="icon.
gif" alt="" /&gt;Products page&lt;/a&gt;</pre>
      <span class="folio">7</span>
      <span class="site">www.qelvantrix.org</span>
    </div>
  </section>
</main>
</body>
</html>
```